Fenwick Grading LTD - website for irrigation & Landscape Lighting & Buried service wire

Looking for a website to help promote my business with Irrigation (installation, service, etc) and buried service wire/drainage solutions.

Commercial/Residential

Landscape lighting.

I’ll get photos in the trucks and trailers to upload as well maybe the machine as well.

Target Market(s)

Homeowners who want green grass and beautiful gardens. Beautiful landscape lighting

Industry/Entity Type

Irrigation systems and landscape lighting and buried service wire to homes and offering Drainage soltions.

Coding

Coded - Design and coding required

Number of Pages Required

4 page

Colors
F0912C
F2A743
F7CA91
FBE8D2
FDF5EE

Requirements
Must have
• was hoping to link up my email on fenwickgrading@mailbox-example.net with the website if possible.
Nice to have
• Page for Irrigation, page for landscape lighting, page buried service wire & drainage soltions.

```html
<!DOCTYPE html>
<html lang="en">
<head>
<meta charset="utf-8">
<title>Fenwick Grading LTD – Irrigation, Landscape Lighting &amp; Buried Service Wire</title>
<link rel="stylesheet" href="https://fonts.googleapis.com/css2?family=Montserrat:wght@400;500;600;700;800&family=Poppins:wght@400;500;600&display=swap">
<style>
:root{
  --orange:#F0912C;
  --orange-2:#F2A743;
  --orange-3:#F7CA91;
  --cream:#FBE8D2;
  --cream-2:#FDF5EE;
  --ink:#141414;
  --grey:#6c6c6c;
  --text:#333;
  --white:#fff;
}
*{box-sizing:border-box;margin:0;padding:0}
html,body{width:1200px;height:4196px;overflow:hidden}
body{font-family:"Poppins",sans-serif;color:var(--text);background:var(--white);position:relative}
.section{position:relative;width:1200px}
.heading{font-family:"Montserrat",sans-serif;font-weight:700;text-transform:uppercase;color:var(--ink)}
.section-title{font-size:44px;text-align:center;position:absolute;left:0;right:0}
.title-rule{position:absolute;left:560px;width:80px;height:4px;background:var(--orange);border-radius:2px}
.btn{display:inline-block;font-family:"Montserrat",sans-serif;font-weight:600;font-size:16px;text-decoration:none;border-radius:4px}
.btn-solid{background:var(--orange);color:var(--white);padding:12px 26px}
.btn-outline{border:2px solid var(--white);color:var(--white);padding:10px 22px}
.photo{background:linear-gradient(160deg,#6f7f5a,#3a4a30)}

/* header */
.site-header{position:absolute;top:0;left:0;width:1200px;height:88px;z-index:5}
.brand{position:absolute;left:16px;top:0;width:232px;height:92px;background:var(--white);border-radius:0 0 10px 10px;display:flex;align-items:center;gap:10px;padding:0 14px}
.brand-mark{width:22px;height:22px;background:var(--orange);flex:none}
.brand-name{font-family:"Montserrat",sans-serif;font-weight:700;font-size:19px;line-height:1.1;color:var(--orange);text-transform:uppercase}
.main-nav{position:absolute;left:270px;top:35px;display:flex;gap:14px;white-space:nowrap}
.main-nav a{font-family:"Montserrat",sans-serif;font-size:11px;font-weight:500;color:var(--white);text-decoration:none;text-transform:uppercase}
.header-cta{position:absolute;right:70px;top:22px;padding:12px 24px;font-size:15px}

/* hero */
.hero{height:660px}
.hero-photo{position:absolute;inset:0;background:linear-gradient(180deg,#2b2e34 0%,#4a3d30 55%,#2f3a25 100%)}
.hero-shade{position:absolute;inset:0;background:linear-gradient(90deg,rgba(0,0,0,.55),rgba(0,0,0,0) 60%)}
.hero-title{position:absolute;left:104px;top:232px;width:460px;font-size:31px;line-height:1.3;color:var(--white)}
.hero .btn-outline{position:absolute;left:104px;top:446px;font-size:15px;padding:10px 18px}
.wave{position:absolute;left:0;width:1200px}

/* services */
.services{height:660px}
.services .section-title{top:76px}
.services .title-rule{top:140px}
.service-card{position:absolute;top:188px;width:310px;height:408px;border-radius:16px;overflow:hidden;box-shadow:0 8px 20px rgba(0,0,0,.18)}
.service-card .photo{position:absolute;inset:0}
.service-card .label{position:absolute;left:0;right:0;bottom:0;height:120px;padding-top:70px;text-align:center;font-family:"Montserrat",sans-serif;font-weight:600;font-size:20px;color:var(--white);background:linear-gradient(180deg,rgba(0,0,0,0),rgba(0,0,0,.7))}
.slider-arrow{position:absolute;width:40px;height:40px;border-radius:50%;border:2px solid var(--orange);background:var(--white);display:flex;align-items:center;justify-content:center}

/* about */
.about{height:580px}
.about-bg{position:absolute;left:0;top:40px;width:1200px;height:500px;background:linear-gradient(180deg,#5e5e5e,#777)}
.about-mark{position:absolute;left:110px;top:200px;width:380px;font-family:"Montserrat",sans-serif;font-weight:800;font-size:46px;line-height:1.1;color:var(--orange);text-transform:uppercase}
.about-title{position:absolute;left:600px;top:118px;font-size:44px;color:var(--white)}
.about .title-rule{left:600px;top:176px}
.about-copy{position:absolute;left:600px;top:196px;width:470px;font-size:14px;line-height:1.6;color:var(--white)}
.about .btn-solid{position:absolute;left:600px;top:448px;font-size:15px;padding:10px 20px}

/* gallery */
.gallery{height:940px}
.gallery .section-title{top:92px}
.gallery .title-rule{top:156px}
.gallery-item{position:absolute;width:322px;height:320px;border-radius:12px}

/* cta */
.cta{height:360px}
.cta-band{position:absolute;left:0;top:40px;width:1200px;height:280px;background:linear-gradient(90deg,#b8751f,var(--orange) 50%,#c27a24)}
.cta-title{position:absolute;left:0;right:0;top:120px;text-align:center;font-size:26px;line-height:1.4;color:var(--white)}
.cta .btn-outline{position:absolute;left:532px;top:222px;font-size:15px;padding:8px 20px}

/* testimonials */
.clients{height:600px}
.clients .section-title{top:100px;font-size:42px}
.clients .title-rule{top:160px}
.review{position:absolute;top:200px;width:310px;height:360px;background:var(--white);border-radius:10px;box-shadow:0 4px 18px rgba(0,0,0,.14);text-align:center;padding-top:18px}
.avatar{width:100px;height:100px;border-radius:50%;margin:0 auto;background:linear-gradient(160deg,var(--orange-3),var(--orange-2))}
.review-name{margin-top:10px;font-family:"Montserrat",sans-serif;font-weight:600;font-size:16px;color:var(--ink)}
.review-role{font-size:13px;color:#888}
.quote{position:absolute;left:22px;top:176px;font-family:"Montserrat",sans-serif;font-size:40px;font-weight:800;color:var(--ink);line-height:1}
.review-text{position:absolute;left:54px;top:182px;width:230px;text-align:left;font-size:13px;line-height:1.6;color:#555}
.stars{position:absolute;left:0;right:0;top:302px;display:flex;justify-content:center;gap:3px}

/* footer */
.site-footer{height:396px;background:#0b0b0b;color:var(--white)}
.footer-brand{position:absolute;left:110px;top:100px;width:240px;display:flex;align-items:center;gap:12px}
.footer-brand .brand-name{color:var(--white);font-size:22px}
.footer-brand .brand-mark{background:var(--white)}
.socials{position:absolute;left:110px;top:220px;display:flex;gap:14px}
.socials span{width:32px;height:32px;border-radius:50%;border:2px solid var(--white)}
.footer-col{position:absolute;top:96px}
.footer-col h3{font-family:"Montserrat",sans-serif;font-weight:700;font-size:22px;margin-bottom:18px}
.footer-col li{list-style:none;font-size:15px;line-height:28px}
.contact-line{display:flex;gap:8px;align-items:flex-start}
.contact-line svg{flex:none;margin-top:8px}
.footer-rule{position:absolute;left:100px;right:100px;top:346px;height:1px;background:#555}
.copyright{position:absolute;left:0;right:0;top:358px;text-align:center;font-size:14px}
</style>
</head>
<body>

<header class="site-header">
  <div class="brand"><span class="brand-mark"></span><span class="brand-name">Fenwick Grading LTD</span></div>
  <nav class="main-nav">
    <a href="#">Home</a><a href="#">About Us</a><a href="#">Irrigation</a><a href="#">Service</a><a href="#">Landscape Lighting</a><a href="#">Buried Service Wire Installation</a>
  </nav>
  <a class="btn btn-solid header-cta" href="#">Contact Us</a>
</header>

<section class="section hero">
  <div class="hero-photo" role="img" aria-label="Modern home at dusk with glowing windows and lit lawn"></div>
  <div class="hero-shade"></div>
  <h1 class="heading hero-title">Homeowners who want green grass and beautiful gardens, beautiful landscape lighting</h1>
  <a class="btn btn-outline" href="#">Get Started</a>
  <svg class="wave" style="top:560px" width="1200" height="100" viewBox="0 0 1200 100" preserveAspectRatio="none">
    <path d="M0 60 Q600 -10 1200 40 L1200 100 L0 100Z" fill="var(--orange)"/>
    <path d="M0 72 Q600 0 1200 52 L1200 100 L0 100Z" fill="#fff"/>
  </svg>
</section>

<section class="section services">
  <h2 class="heading section-title">Our Services</h2>
  <div class="title-rule"></div>
  <div class="slider-arrow" style="left:30px;top:372px"><svg width="14" height="14" viewBox="0 0 14 14"><path d="M9 2 L4 7 L9 12" stroke="var(--orange)" stroke-width="2.5" fill="none"/></svg></div>
  <article class="service-card" style="left:100px">
    <div class="photo" role="img" aria-label="Sprinklers watering a green lawn and garden bed"></div>
    <div class="label">Irrigation Installs</div>
  </article>
  <article class="service-card" style="left:445px">
    <div class="photo" style="background:linear-gradient(160deg,#c98f6a,#4a3a36)" role="img" aria-label="House facade lit by landscape lights at night"></div>
    <div class="label">Landscape Lighting</div>
  </article>
  <article class="service-card" style="left:790px">
    <div class="photo" style="background:linear-gradient(160deg,#5b6470,#2c2f36)" role="img" aria-label="Technician testing buried service cable with a meter"></div>
    <div class="label">Buried Service Wire</div>
  </article>
  <div class="slider-arrow" style="left:1128px;top:372px"><svg width="14" height="14" viewBox="0 0 14 14"><path d="M5 2 L10 7 L5 12" stroke="var(--orange)" stroke-width="2.5" fill="none"/></svg></div>
</section>

<section class="section about">
  <svg class="wave" style="top:0" width="1200" height="80" viewBox="0 0 1200 80" preserveAspectRatio="none">
    <path d="M0 40 Q600 0 1200 50 L1200 80 L0 80Z" fill="#5e5e5e"/>
  </svg>
  <div class="about-bg"></div>
  <svg class="wave" style="top:500px" width="1200" height="80" viewBox="0 0 1200 80" preserveAspectRatio="none">
    <path d="M0 0 L1200 0 L1200 30 Q600 80 0 40Z" fill="#777"/>
  </svg>
  <div class="about-mark">Fenwick Grading LTD</div>
  <h2 class="heading about-title">About Us</h2>
  <div class="title-rule"></div>
  <p class="about-copy">Lorem Ipsum is simply dummy text of the printing and typesetting industry. Lorem Ipsum has been the industry's standard dummy text ever since the 1500s, when an unknown printer took a galley of type and scrambled it to make a type specimen book. It has survived not only five centuries, but also the leap into electronic typesetting, remaining essentially unchanged. It was popularised in the 1960s with the release of Letraset sheets containing Lorem Ipsum passages, and more recently with desktop publishing software like Aldus.</p>
  <a class="btn btn-solid" href="#">Read More</a>
</section>

<section class="section gallery">
  <h2 class="heading section-title">Our Gallery</h2>
  <div class="title-rule"></div>
  <div class="gallery-item photo" style="left:88px;top:200px;background:linear-gradient(160deg,#7a8ea8,#3e4a3a)" role="img" aria-label="Blue two-storey house with front lawn"></div>
  <div class="gallery-item photo" style="left:438px;top:200px;background:linear-gradient(160deg,#9aa8b5,#5d7a45)" role="img" aria-label="Curved garden path to a grey house"></div>
  <div class="gallery-item photo" style="left:786px;top:200px;background:linear-gradient(160deg,#3a2b22,#b57a3a)" role="img" aria-label="Garden lights along a stone walkway at night"></div>
  <div class="gallery-item photo" style="left:88px;top:548px;background:linear-gradient(160deg,#2e3440,#c48a4a)" role="img" aria-label="Modern home and driveway lit at dusk"></div>
  <div class="gallery-item photo" style="left:438px;top:548px;background:linear-gradient(160deg,#6e8a5a,#3a5a2e)" role="img" aria-label="Layered shrub garden with stone wall"></div>
  <div class="gallery-item photo" style="left:786px;top:548px;background:linear-gradient(160deg,#8a9ab0,#6d7a5a)" role="img" aria-label="Grey house with garage and lawn"></div>
</section>

<section class="section cta">
  <div class="cta-band" role="img" aria-label="Warm orange background of a lit garden"></div>
  <svg class="wave" style="top:300px" width="1200" height="60" viewBox="0 0 1200 60" preserveAspectRatio="none">
    <path d="M0 20 Q600 -10 1200 30 L1200 60 L0 60Z" fill="#666"/>
    <path d="M0 34 Q600 4 1200 44 L1200 60 L0 60Z" fill="#fff"/>
  </svg>
  <h2 class="heading cta-title">Irrigation systems and landscape lighting and buried<br>service wire installation to homes</h2>
  <a class="btn btn-outline" href="#">Contact Us</a>
</section>

<section class="section clients">
  <h2 class="heading section-title">What Our Clients Say</h2>
  <div class="title-rule"></div>
  <div class="slider-arrow" style="left:28px;top:360px"><svg width="14" height="14" viewBox="0 0 14 14"><path d="M9 2 L4 7 L9 12" stroke="var(--orange)" stroke-width="2.5" fill="none"/></svg></div>

  <article class="review" style="left:112px">
    <div class="avatar" role="img" aria-label="Client portrait"></div>
    <div class="review-name">Anderson</div><div class="review-role">Client</div>
    <span class="quote">“</span>
    <p class="review-text">Lorem Ipsum is simply dummy text of the printing and typesetting industry. Lorem Ipsum has been the industry's standard dummy text ever since the</p>
    <div class="stars"><svg width="100" height="18" viewBox="0 0 100 18"><g fill="var(--orange)"><path id="s" d="M9 1 L11.3 6.5 L17 7 L12.6 10.8 L14 16.5 L9 13.5 L4 16.5 L5.4 10.8 L1 7 L6.7 6.5Z"/><use href="#s" x="20"/><use href="#s" x="40"/><use href="#s" x="60"/><use href="#s" x="80"/></g></svg></div>
  </article>
  <article class="review" style="left:445px">
    <div class="avatar" role="img" aria-label="Client portrait"></div>
    <div class="review-name">Robin</div><div class="review-role">Client</div>
    <span class="quote">“</span>
    <p class="review-text">Lorem Ipsum is simply dummy text of the printing and typesetting industry. Lorem Ipsum has been the industry's standard dummy text ever since the</p>
    <div class="stars"><svg width="100" height="18" viewBox="0 0 100 18"><g fill="var(--orange)"><use href="#s"/><use href="#s" x="20"/><use href="#s" x="40"/><use href="#s" x="60"/><use href="#s" x="80"/></g></svg></div>
  </article>
  <article class="review" style="left:778px">
    <div class="avatar" role="img" aria-label="Client portrait"></div>
    <div class="review-name">Jessica</div><div class="review-role">Client</div>
    <span class="quote">“</span>
    <p class="review-text">Lorem Ipsum is simply dummy text of the printing and typesetting industry. Lorem Ipsum has been the industry's standard dummy text ever since the</p>
    <div class="stars"><svg width="100" height="18" viewBox="0 0 100 18"><g fill="var(--orange)"><use href="#s"/><use href="#s" x="20"/><use href="#s" x="40"/><use href="#s" x="60"/><use href="#s" x="80"/></g></svg></div>
  </article>

  <div class="slider-arrow" style="left:1128px;top:360px"><svg width="14" height="14" viewBox="0 0 14 14"><path d="M5 2 L10 7 L5 12" stroke="var(--orange)" stroke-width="2.5" fill="none"/></svg></div>
</section>

<footer class="section site-footer">
  <div class="footer-brand"><span class="brand-mark"></span><span class="brand-name">Fenwick<br>Grading LTD</span></div>
  <div class="socials"><span></span><span></span><span></span></div>

  <div class="footer-col" style="left:396px">
    <h3>Quick links</h3>
    <ul><li>Home</li><li>About Us</li><li>Services</li><li>Testimonials</li><li>Contact Us</li></ul>
  </div>
  <div class="footer-col" style="left:620px">
    <h3>Service Links</h3>
    <ul><li>Irrigation Service</li><li>Landscape Lighting</li><li>Buried Service Wire</li></ul>
  </div>
  <div class="footer-col" style="left:860px">
    <h3>Contact Info</h3>
    <ul>
      <li class="contact-line"><svg width="14" height="11" viewBox="0 0 14 11"><rect x="0.5" y="0.5" width="13" height="10" fill="none" stroke="#fff"/><path d="M1 1 L7 6 L13 1" fill="none" stroke="#fff"/></svg><span style="font-size:13px">fenwickgrading@mailbox-example.net</span></li>
      <li class="contact-line"><svg width="12" height="12" viewBox="0 0 12 12"><path d="M2 1 L4.5 1 L5.5 4 L4 5 Q5 7.5 7 8 L8 6.5 L11 7.5 L11 10 Q5 11 1 4Z" fill="#fff"/></svg><span>+1888-555-0142</span></li>
      <li class="contact-line"><svg width="12" height="14" viewBox="0 0 12 14"><path d="M6 13 Q1 7 1 5 A5 5 0 0 1 11 5 Q11 7 6 13Z" fill="#fff"/><circle cx="6" cy="5" r="1.8" fill="#0b0b0b"/></svg><span>100 Lorem Ipsum<br>is Simply Lorem Ipsum</span></li>
    </ul>
  </div>
  <div class="footer-rule"></div>
  <p class="copyright">Copyright © 2024 Fenwick Grading | All Rights Reserved</p>
</footer>

</body>
</html>
```